Stationery Design Project

I need a design that is simple, clean and modern, in square style, bold font.
The majority of the design needs to be White and Black with a splash of Red colour.
I would like a design for business cards and letter heads with the following information.
Name, Title, Phone, Fax, Email, Website and company ABN number

Target Market(s)

25 to 65 years old real estate clients

Industry/Entity Type

Business

Requirements
Must have
• All designs must incorporate Company Logo, Name, Title, Phone, Fax, Email, Website and company ABN number

```html
<!DOCTYPE html>
<html lang="en">
<head>
<meta charset="utf-8">
<title>Ravenmoor Real Estate – Business Card</title>
<link href="https://fonts.googleapis.com/css2?family=Open+Sans:wght@400;600;700&display=swap" rel="stylesheet">
<style>
  :root {
    --backdrop: #e8e5e1;
    --card-white: #ffffff;
    --ink: #231f20;
    --accent-red: #b3202e;
    --paper-text: #ffffff;
    --muted: #555555;
  }
  * { box-sizing: border-box; margin: 0; padding: 0; }
  html, body {
    width: 1200px; height: 402px; overflow: hidden;
    background: var(--backdrop);
    font-family: "Open Sans", Arial, sans-serif;
  }
  .stage { position: relative; width: 1200px; height: 402px; }

  .card {
    position: absolute; top: 55px;
    width: 511px; height: 292px; overflow: hidden;
    box-shadow: 0 2px 8px rgba(0,0,0,.25);
  }
  .card--front { left: 61px; background: var(--card-white); }
  .card--back  { left: 631px; background: var(--ink); }

  .holder-name {
    position: absolute; top: 12px; width: 100%;
    text-align: center; font-size: 15px; color: #444;
  }
  .holder-name strong { font-weight: 700; }

  .brand-frame {
    position: absolute; display: flex; flex-direction: column;
    align-items: center; justify-content: center;
    border-radius: 16px; font-weight: 600;
  }
  .card--front .brand-frame {
    left: 148px; top: 51px; width: 217px; height: 121px;
    border: 4px solid var(--ink); color: var(--ink);
  }
  .card--back .brand-frame {
    left: 104px; top: 42px; width: 306px; height: 168px;
    border: 4px solid var(--paper-text); color: var(--paper-text);
  }
  .brand-name { font-size: 26px; letter-spacing: 1px; line-height: 1.1; }
  .brand-tag  { font-size: 12px; letter-spacing: 7px; margin-top: 6px; }
  .card--back .brand-name { font-size: 38px; }
  .card--back .brand-tag  { font-size: 16px; letter-spacing: 10px; margin-top: 10px; }

  .footer-shape { position: absolute; left: 0; top: 0; }

  .contact-row {
    position: absolute; left: 0; top: 248px; width: 100%;
    display: flex; align-items: center; color: var(--paper-text);
    font-size: 13px; line-height: 19px;
  }
  .contact-col { padding: 0 12px; }
  .contact-col--phones { padding-left: 38px; }
  .contact-col + .contact-col { border-left: 1.5px solid var(--paper-text); }
  .contact-line { display: flex; align-items: center; gap: 4px; white-space: nowrap; }
  .contact-line svg { width: 11px; height: 11px; fill: var(--paper-text); }

  .abn {
    position: absolute; top: 232px; width: 100%; text-align: center;
    color: var(--paper-text); font-size: 16px;
  }
</style>
</head>
<body>
<main class="stage">

  <section class="card card--front">
    <p class="holder-name"><strong>Your Name,</strong> Title</p>

    <div class="brand-frame">
      <span class="brand-name">RAVENMOOR</span>
      <span class="brand-tag">REAL ESTATE</span>
    </div>

    <svg class="footer-shape" width="511" height="292" viewBox="0 0 511 292">
      <path d="M0 240 Q255 150 511 245 L511 250 Q255 165 0 246 Z" fill="var(--accent-red)"/>
      <path d="M0 250 Q255 175 511 256 L511 292 L0 292 Z" fill="var(--ink)"/>
    </svg>

    <div class="contact-row">
      <div class="contact-col contact-col--phones">
        <div class="contact-line">
          <svg viewBox="0 0 24 24"><path d="M6.6 10.8a15 15 0 0 0 6.6 6.6l2.2-2.2c.3-.3.7-.4 1-.2 1.1.4 2.3.6 3.6.6.6 0 1 .4 1 1V20c0 .6-.4 1-1 1A17 17 0 0 1 3 4c0-.6.4-1 1-1h3.5c.6 0 1 .4 1 1 0 1.3.2 2.5.6 3.6.1.3 0 .7-.2 1z"/></svg>
          123-456-7890
        </div>
        <div class="contact-line">
          <svg viewBox="0 0 24 24"><path d="M6 3h10v5H6zM3 9h18v9h-3v3H6v-3H3zM8 15v4h8v-4z"/></svg>
          123-456-7890
        </div>
      </div>
      <div class="contact-col">
        <div class="contact-line">
          <svg viewBox="0 0 24 24"><path d="M2 5h20v14H2zm2 2v.5l8 5 8-5V7z"/></svg>
          info@harbourmail.com
        </div>
        <div class="contact-line">
          <svg viewBox="0 0 24 24"><circle cx="12" cy="12" r="10"/></svg>
          www.website.com
        </div>
      </div>
      <div class="contact-col">
        <div class="contact-line">Street Name, City Name</div>
        <div class="contact-line">State, City Zip Code 000</div>
      </div>
    </div>
  </section>

  <section class="card card--back">
    <div class="brand-frame">
      <span class="brand-name">RAVENMOOR</span>
      <span class="brand-tag">REAL ESTATE</span>
    </div>
    <p class="abn">ABN;123456789</p>
  </section>

</main>
</body>
</html>
```